IT consulting company looking for a modern business design for a website and a new logo

We are the IT-consulting company VelmaTrix from Germany and need a new and modern business website and a new logo. We are specialized in output management. Our services include business analysis, outsourcing, development, training and project leading. We wish for a design with nature pictures (mountains, lakes, rivers, forests, etc.) for our company with the colors green and blue. If it is possible, a slow-mo video of a nature scene. The design should be responsive and the menu should change to a hamburger menu. The following are: • Services / Solutions 1. Output Management 2. Outsourcing 3. Development 4. Business Analyst 5. Training • Partners • Careers • About Us 1. Project A 2. Project B 3. Project C • Contact Notes for the following categories: For "Services / Solutions" we want to conclude some contents from all the sub-points and sub-points below. Additionally, we would like to see some sub-point under "Services / Solutions". For Output Management: "5 Benefits of Output Management Systems (OMS) - OMS Simplifies and Accelerates External Communication - Helps Reduce Communication Mistakes - Provides Customers With Fast and Secure Responses to your questions - Employees can focus on the essential as they can access prepared templates - Companies get complete transparency about their communication "The point" partner does not have sub-points. The content here is a quote and the logo from the company Brel. For now, just placeholders on this site. The next point wants to be "career" without sub-point and wants to contain some text. Carrer options wants to be listed here. Next point wants to be "About us", where we need sub-points which we do not know exactly at this moment, but they will contain text. By clicking directly on "About us" we want to include pictures and texts about 6 employees for which we only need placeholders at the moment. The last point wants to be "contact", where customers can send us messages. The main page should include a story about our company, which can be a placeholder for now. For reference, designs have a look at: https://brelvanto.de/ https://www.tarnopix.com/ https://www.pldrive.de/ We prefer WordPress designs, created with the plugin ELEMENTOR, so that we can easily edit the content by ourselves. The final design should look professional, competent and modern.

Target Market(s)

With our website, we want to reach the following target groups. <br> <br> <br> <br> <br> <br> <br> <br> <br> <br> <br> <br> <br> <br> <br> <br> <br> <br> <br> <br> <br> <br> <br> <br> <br> <br> <br> <br> <br> <br> <br> <br> <br> <br> <br> <br> <br> <br> <br> <br> <br> <br> <br> <br> <br> <br> <br> <br> <br>

Industry/Entity Type

Consulting

Logo Text

(optionally) VelmaTrix

Font styles to use
Sans Serif

Colors

Designer to choose colors to be used in the design.

Requirements
Must have
• 1. Outsourcing 3. Development 4. Business Analyst 5. Training • Partners • Careers • About Us 1. Project A 2. Project B 3. Project C • Contact The above-mentioned background picture with nature motifs (mountains, lakes, rivers, forests, etc.). WordPress design in primary colors blue and green.
Nice to have
• ELEMENTOR template. Effects for the background pictures. Counter of all successful projects for Output Management, Business Analyst and Training

```html
<!DOCTYPE html>
<html lang="en">
<head>
<meta charset="utf-8">
<title>VelmaTrix – IT Consulting</title>
<link rel="stylesheet" href="https://fonts.googleapis.com/css2?family=Poppins:wght@400;500;600;700&display=swap">
<style>
:root{
  --blue:#2b8ae0;
  --blue-dark:#1b63b0;
  --green:#2fa36b;
  --green-dark:#1f7a4f;
  --navy:#0d2a4d;
  --ink:#2d2d2d;
  --muted:#555;
  --nav-bg:#f1f1f1;
  --line:#e4e4e4;
  --white:#fff;
}
*{box-sizing:border-box;margin:0;padding:0}
html,body{width:1200px;height:4605px;overflow:hidden}
body{position:relative;font-family:'Poppins',sans-serif;color:var(--ink);background:var(--white)}
.abs{position:absolute}
.center{text-align:center;left:0;width:1200px}

.topbar{top:0;left:0;width:1200px;height:40px;background:linear-gradient(90deg,var(--blue),var(--green));color:var(--white);font-size:13px}
.topbar span{position:absolute;top:11px}
.topbar svg{vertical-align:-2px;margin-right:5px}

.header{top:40px;left:0;width:1200px;height:112px}
.call-icon{left:110px;top:36px;width:40px;height:40px;border:2px solid var(--blue);border-radius:50%;display:flex;align-items:center;justify-content:center}
.call-text{left:161px;top:30px;font-size:14px;line-height:22px}
.call-text b{display:block;color:var(--blue);font-weight:400;font-size:13px}
.call-text strong{font-weight:500;font-size:16px}
.brand{left:0;width:1200px;text-align:center;top:34px;font-size:34px;font-weight:700;color:var(--blue);letter-spacing:.5px}
.search{left:788px;top:32px;width:299px;height:51px;border:2px solid var(--line);border-radius:26px;font-size:15px;color:#999;padding:13px 20px}
.search i{position:absolute;right:6px;top:6px;width:37px;height:37px;border-radius:50%;background:var(--green);display:flex;align-items:center;justify-content:center}

.nav{top:152px;left:0;width:1200px;height:66px;background:var(--nav-bg);border-top:1px solid var(--line)}
.nav a{position:absolute;top:20px;font-size:17px;color:var(--ink);text-decoration:none}
.appoint{left:828px;top:0;width:282px;height:66px;background:var(--green);color:var(--white);font-size:16px;display:flex;align-items:center;justify-content:center;gap:12px}

.hero{top:218px;left:0;width:1200px;height:570px;background:linear-gradient(180deg,#123a5e 0%,#1e5f86 35%,#2f7a6a 62%,#1d4d35 85%,#153626 100%)}
.hero-title{left:89px;top:150px;font-size:56px;font-weight:600;color:var(--white)}
.hero-sub{left:89px;top:225px;width:500px;font-size:18px;font-weight:600;color:var(--white);line-height:36px}
.btn{position:absolute;height:52px;border-radius:26px;font-size:17px;font-weight:600;display:flex;align-items:center;justify-content:center;gap:8px}
.btn-solid{background:var(--white);color:var(--blue)}
.btn-ghost{border:3px solid var(--white);color:var(--white)}
.btn-line{border:3px solid var(--white);color:var(--white);font-size:16px}

h2.title{position:absolute;left:0;width:1200px;text-align:center;font-size:34px;font-weight:600;color:var(--blue)}
.lead{position:absolute;left:140px;width:920px;text-align:center;font-size:15.5px;line-height:36px;color:var(--ink)}

.service{position:absolute;top:1110px;width:196px;height:196px;border-radius:50%;background:linear-gradient(135deg,var(--blue),var(--green));padding:5px}
.service-face{width:100%;height:100%;border-radius:50%;display:flex;flex-direction:column;align-items:center;justify-content:center;color:var(--white);text-align:center;position:relative}
.service-face::after{content:"";position:absolute;inset:10px;border:1px dashed rgba(255,255,255,.7);border-radius:50%}
.service h3{font-size:19px;font-weight:600;line-height:23px;margin-bottom:6px}
.service p{font-size:10.5px;line-height:18px;width:140px;opacity:.92}
.dots{position:absolute;left:0;width:1200px;display:flex;justify-content:center;gap:8px}
.dots i{width:16px;height:16px;border-radius:50%;background:var(--green)}
.dots i:first-child{background:var(--white);border:2px solid var(--blue)}
.dots i:last-child{background:var(--blue)}

.band{left:0;width:1200px}
.photo-round{position:absolute;border-radius:50%;border:10px solid var(--white);box-shadow:0 0 0 10px var(--green)}
.band-text{color:var(--white)}
.band-text h2{font-size:34px;font-weight:600;margin-bottom:10px}
.band-text p{font-size:15.5px;line-height:36px;text-align:justify}

.partner{position:absolute;width:247px;height:136px;background:var(--white);box-shadow:0 0 6px rgba(0,0,0,.15);display:flex;align-items:center;justify-content:center;gap:10px;font-size:22px;font-weight:600;color:var(--blue-dark)}
.partner i{width:22px;height:22px;background:var(--green)}

.info{position:absolute;top:3701px;width:300px;text-align:center;font-size:16px;line-height:28px;color:var(--ink)}
.info .ic{width:84px;height:84px;border-radius:50%;background:linear-gradient(135deg,var(--blue),var(--green));margin:0 auto 12px;display:flex;align-items:center;justify-content:center}
.field{position:absolute;height:40px;border:1px solid var(--line);box-shadow:inset 0 2px 3px rgba(0,0,0,.06);font-size:11px;color:#555;padding:12px 16px}
.submit{left:511px;top:4196px;width:177px;height:48px;background:var(--green);color:var(--white);font-size:17px;font-weight:500;display:flex;align-items:center;justify-content:center;gap:8px}

.footer{top:4330px;left:0;width:1200px;height:275px}
.social{position:absolute;top:4461px;left:0;width:1200px;display:flex;justify-content:center;gap:6px}
.social i{width:30px;height:30px;border-radius:50%;border:2px solid var(--white)}
.foot-links{top:4515px;font-size:17px;color:var(--white)}
.foot-links span{margin:0 10px}
.copy{top:4557px;font-size:16px;color:var(--white);letter-spacing:.5px}
</style>
</head>
<body>

<div class="abs topbar">
  <span style="left:107px"><svg width="14" height="11" viewBox="0 0 14 11"><rect x="0.5" y="0.5" width="13" height="10" fill="none" stroke="#fff"/><path d="M1 1l6 5 6-5" fill="none" stroke="#fff"/></svg>info@company.com</span>
  <span style="left:685px">EN ▾</span>
  <span style="left:757px;font-size:12px"><svg width="10" height="13" viewBox="0 0 10 13"><path d="M5 0a5 5 0 0 1 5 5c0 3-5 8-5 8S0 8 0 5a5 5 0 0 1 5-5z" fill="#fff"/><circle cx="5" cy="5" r="2" fill="#2b8ae0"/></svg>Lindenweg 14, Altmark, Niedersachsen - 26510</span>
</div>

<div class="abs header">
  <div class="abs call-icon"><svg width="20" height="20" viewBox="0 0 24 24"><path d="M6.6 10.8a15 15 0 0 0 6.6 6.6l2.2-2.2a1 1 0 0 1 1-.25 11.4 11.4 0 0 0 3.6.57 1 1 0 0 1 1 1V20a1 1 0 0 1-1 1A17 17 0 0 1 3 4a1 1 0 0 1 1-1h3.5a1 1 0 0 1 1 1c0 1.25.2 2.45.57 3.57a1 1 0 0 1-.25 1z" fill="#2b8ae0"/></svg></div>
  <div class="abs call-text"><b>Call us:</b><strong>(888) 888-8888</strong></div>
  <div class="abs brand">VELMATRIX</div>
  <div class="abs search">Search<i><svg width="14" height="14" viewBox="0 0 14 14"><circle cx="6" cy="6" r="4.5" fill="none" stroke="#fff" stroke-width="2"/><path d="M9.5 9.5L13 13" stroke="#fff" stroke-width="2"/></svg></i></div>
</div>

<nav class="abs nav">
  <a style="left:89px">Home</a>
  <a style="left:188px">About Us</a>
  <a style="left:310px">Our Services</a>
  <a style="left:465px">Partner</a>
  <a style="left:574px">Careers</a>
  <a style="left:690px">Contact Us</a>
  <div class="abs appoint"><svg width="18" height="18" viewBox="0 0 24 24"><path d="M22 2L2 10l7 3 3 7z" fill="#fff"/></svg>Get an Appointment</div>
</nav>

<section class="abs hero" role="img" aria-label="Nature photo of a mountain lake with forest on the shore under a blue sky">
  <div class="abs hero-title">VelmaTrix</div>
  <div class="abs hero-sub">Sed ut perspiciatis unde omnis iste natus error sit voluptatem sunt explicabo.</div>
  <div class="btn btn-solid" style="left:89px;top:314px;width:215px"><svg width="12" height="15" viewBox="0 0 12 15"><path d="M0 0h8l4 4v11H0z" fill="#2b8ae0"/></svg>Read More</div>
  <div class="btn btn-ghost" style="left:320px;top:314px;width:186px"><svg width="16" height="16" viewBox="0 0 24 24"><path d="M22 2L2 10l8 4 4 8z" fill="#fff"/></svg>Contact us</div>
  <svg class="abs" style="left:0;bottom:-1px" width="1200" height="40" viewBox="0 0 1200 40" preserveAspectRatio="none"><path d="M0 26 L30 20 60 28 95 18 130 25 170 16 210 24 250 19 300 27 340 17 380 24 430 20 470 28 520 18 560 25 610 19 650 27 700 17 740 23 790 18 830 26 880 20 920 28 970 18 1010 24 1060 19 1100 27 1150 20 1200 24 V40 H0z" fill="#fff"/></svg>
</section>

<h2 class="title" style="top:890px">OUR SERVICES</h2>
<p class="lead" style="top:949px">Sed ut perspiciatis unde omnis iste natus error sit voluptatem accusantium doloremque laudantium, totam rem aperiam, eaque ipsa quae ab illo inventore veritatis et vitae dicta sunt explicabo.</p>

<div class="service" style="left:90px">
  <div class="service-face" role="img" aria-label="Nature photo of a forest river, blue tinted" style="background:radial-gradient(circle at 40% 40%,#2f7fd0,#1a5a8e 70%,#14456a)">
    <h3>Output<br>Management</h3>
    <p>Lorem ipsum dolor sit amet, consectetur adipiscing elit</p>
  </div>
</div>
<div class="service" style="left:296px">
  <div class="service-face" role="img" aria-label="Nature photo of green hills, dark tinted" style="background:radial-gradient(circle at 50% 40%,#2f7a5c,#1d5240 70%,#123a2c)">
    <h3>Outsourcing</h3>
    <p>Lorem ipsum dolor sit amet, consectetur adipiscing elit</p>
  </div>
</div>
<div class="service" style="left:502px">
  <div class="service-face" role="img" aria-label="Nature photo of mountains above a lake, blue tinted" style="background:radial-gradient(circle at 50% 40%,#2d6fb3,#184a82 70%,#0f3260)">
    <h3>Development</h3>
    <p>Lorem ipsum dolor sit amet, consectetur adipiscing elit</p>
  </div>
</div>
<div class="service" style="left:708px">
  <div class="service-face" role="img" aria-label="Nature photo of a pine forest, green tinted" style="background:radial-gradient(circle at 50% 40%,#3a9a6a,#22704a 70%,#154f33)">
    <h3>Business<br>Analysis</h3>
    <p>Lorem ipsum dolor sit amet, consectetur adipiscing elit</p>
  </div>
</div>
<div class="service" style="left:914px">
  <div class="service-face" role="img" aria-label="Nature photo of a calm lake at dawn, blue-green tinted" style="background:radial-gradient(circle at 50% 40%,#2f8ea0,#1d6478 70%,#134a58)">
    <h3>Training</h3>
    <p>Lorem ipsum dolor sit amet, consectetur adipiscing elit</p>
  </div>
</div>
<div class="dots" style="top:1419px"><i></i><i></i><i></i></div>

<section class="abs band" style="top:1484px;height:626px">
  <svg class="abs" style="left:0;top:0" width="1200" height="626" viewBox="0 0 1200 626">
    <defs><linearGradient id="bandA" x1="0" y1="0" x2="1" y2="1"><stop offset="0" stop-color="#2b8ae0"/><stop offset="1" stop-color="#2fa36b"/></linearGradient></defs>
    <polygon points="0,134 1200,5 1200,622 0,479" fill="url(#bandA)"/>
  </svg>
  <div class="photo-round" role="img" aria-label="Photo of a hand raised with a pen during a team meeting" style="left:54px;top:128px;width:428px;height:428px;background:linear-gradient(135deg,#cfc7bd,#8c7f74 55%,#4a4540)"></div>
  <div class="abs band-text" style="left:551px;top:140px;width:559px">
    <h2>ABOUT US</h2>
    <p>Sed ut perspiciatis unde omnis iste natus error sit voluptatem accusantium doloremque laudantium, totam rem aperiam, eaque ipsa quae ab illo inventore veritatis et quasi architecto beatae vitae dicta sunt explicabo. Nemo enim ipsam voluptatem quia voluptas sit aspernatur aut odit aut fugit, sed quia consequuntur magni dolores eos qui ratione voluptatem sequi nesciunt.</p>
  </div>
  <div class="btn btn-line" style="left:551px;top:424px;width:187px">Read More <svg width="16" height="16" viewBox="0 0 16 16"><circle cx="8" cy="8" r="6.5" fill="none" stroke="#fff" stroke-width="1.5"/><path d="M5 8h6M8.5 5.5L11 8l-2.5 2.5" fill="none" stroke="#fff" stroke-width="1.5"/></svg></div>
</section>

<h2 class="title" style="top:2210px">PARTNERS</h2>
<svg class="abs" style="left:574px;top:2296px" width="52" height="40" viewBox="0 0 52 40"><path d="M0 0h22v22l-8 18H5l7-16H0zM30 0h22v22l-8 18h-9l7-16H30z" fill="#555"/></svg>
<p class="lead" style="top:2365px">Sed ut perspiciatis unde omnis iste natus error sit voluptatem accusantium doloremque laudantium, totam rem aperiam, eaque ipsa quae ab illo inventore vitae dicta sunt explicabo.</p>

<div class="partner" style="left:89px;top:2465px"><i></i>Aventro</div>
<div class="partner" style="left:347px;top:2465px">Halvora</div>
<div class="partner" style="left:605px;top:2465px"><i></i>Ostrellis</div>
<div class="partner" style="left:862px;top:2465px">Banca Verlina</div>
<div class="partner" style="left:89px;top:2615px">Bank Zelvora</div>
<div class="partner" style="left:347px;top:2615px"><i></i>Mirvessa</div>
<div class="partner" style="left:605px;top:2615px;font-size:19px">Calveth Partners</div>
<div class="partner" style="left:862px;top:2615px">Noviq</div>
<div class="dots" style="top:2781px"><i></i><i></i><i></i></div>

<section class="abs band" style="top:2860px;height:625px">
  <svg class="abs" style="left:0;top:0" width="1200" height="625" viewBox="0 0 1200 625">
    <defs><linearGradient id="bandC" x1="0" y1="0" x2="1" y2="1"><stop offset="0" stop-color="#2fa36b"/><stop offset="1" stop-color="#2b8ae0"/></linearGradient></defs>
    <polygon points="0,4 1200,90 1200,548 0,620" fill="url(#bandC)"/>
  </svg>
  <div class="abs band-text" style="left:97px;top:140px;width:558px">
    <h2>CAREERS</h2>
    <p>Sed ut perspiciatis unde omnis iste natus error sit voluptatem accusantium doloremque laudantium, totam rem aperiam, eaque ipsa quae ab illo inventore veritatis et quasi architecto beatae vitae dicta sunt explicabo. Nemo enim ipsam voluptatem quia voluptas sit aspernatur aut odit aut fugit, sed quia consequuntur magni dolores eos qui ratione voluptatem sequi nesciunt.</p>
  </div>
  <div class="btn btn-line" style="left:97px;top:422px;width:187px">Apply Now <svg width="16" height="16" viewBox="0 0 16 16"><circle cx="8" cy="8" r="6.5" fill="none" stroke="#fff" stroke-width="1.5"/><path d="M5 8h6M8.5 5.5L11 8l-2.5 2.5" fill="none" stroke="#fff" stroke-width="1.5"/></svg></div>
  <div class="photo-round" role="img" aria-label="Photo of three colleagues at a laptop in a bright office" style="left:705px;top:100px;width:438px;height:438px;background:linear-gradient(135deg,#f3f1ee,#d9d2c8 50%,#e0b640 80%,#c79a2c)"></div>
</section>

<h2 class="title" style="top:3583px">CONTACT INFORMATION</h2>
<div class="abs center" style="top:3641px;font-size:19px;font-weight:500;color:var(--muted)">Contact us for more information</div>

<div class="info" style="left:154px">
  <div class="ic"><svg width="40" height="44" viewBox="0 0 40 44"><path d="M20 4a12 12 0 0 1 12 12c0 9-12 22-12 22S8 25 8 16A12 12 0 0 1 20 4z" fill="none" stroke="#fff" stroke-width="2"/><circle cx="20" cy="16" r="4.5" fill="none" stroke="#fff" stroke-width="2"/><path d="M10 40h20" stroke="#fff" stroke-width="2"/></svg></div>
  Lindenweg 14, Altmark<br>Niedersachsen - 26510
</div>
<div class="info" style="left:460px">
  <div class="ic"><svg width="40" height="40" viewBox="0 0 24 24"><path d="M6.6 10.8a15 15 0 0 0 6.6 6.6l2.2-2.2a1 1 0 0 1 1-.25 11.4 11.4 0 0 0 3.6.57 1 1 0 0 1 1 1V20a1 1 0 0 1-1 1A17 17 0 0 1 3 4a1 1 0 0 1 1-1h3.5a1 1 0 0 1 1 1c0 1.250.2 2.45.57 3.57a1 1 0 0 1-.25 1z" fill="none" stroke="#fff" stroke-width="1.2"/></svg></div>
  Phone:<br>+1 888 888 8888
</div>
<div class="info" style="left:765px">
  <div class="ic"><svg width="44" height="32" viewBox="0 0 44 32"><rect x="1" y="1" width="42" height="30" fill="none" stroke="#fff" stroke-width="2"/><path d="M1 1l21 17L43 1M1 31l16-15M43 31L27 16" fill="none" stroke="#fff" stroke-width="2"/></svg></div>
  Email:<br>info@company.com
</div>

<h2 class="title" style="top:3906px">CONTACT US</h2>
<div class="field" style="left:161px;top:3980px;width:431px">👤 First Name</div>
<div class="field" style="left:610px;top:3980px;width:429px">👤 Last Name</div>
<div class="field" style="left:161px;top:4035px;width:431px">▮ Company</div>
<div class="field" style="left:610px;top:4035px;width:429px;height:145px">✎ Message :</div>
<div class="field" style="left:161px;top:4088px;width:431px">✉ Email Address</div>
<div class="field" style="left:161px;top:4141px;width:431px">☏ Phone Number</div>
<div class="abs submit"><svg width="16" height="16" viewBox="0 0 24 24"><path d="M22 2L2 10l8 4 4 8z" fill="#fff"/></svg>Submit</div>

<footer class="abs footer">
  <svg class="abs" style="left:0;top:0" width="1200" height="275" viewBox="0 0 1200 275" preserveAspectRatio="none">
    <defs><linearGradient id="foot" x1="0" y1="0" x2="1" y2="1"><stop offset="0" stop-color="#2b8ae0"/><stop offset="1" stop-color="#2fa36b"/></linearGradient></defs>
    <path d="M0 40 L25 30 55 38 85 22 120 34 150 26 190 36 230 20 270 32 310 24 350 36 390 22 430 30 470 18 510 34 550 26 590 36 630 20 670 30 710 24 750 36 790 22 830 32 870 26 910 36 950 20 990 30 1030 24 1070 36 1110 22 1150 32 1200 26 V275 H0z" fill="url(#foot)"/>
  </svg>
</footer>
<div class="social"><i></i><i></i><i></i><i></i></div>
<div class="abs center foot-links">Home<span>|</span>About Us<span>|</span>Our Services<span>|</span>Careers<span>|</span>Our Partners<span>|</span>Contact Us</div>
<div class="abs center copy">Copyright © 2019. All Rights Reserved.</div>

</body>
</html>
```